Design website for new email startup

We are starting a company called Pingo.QZ (it will live at http://pingo.qz).

We would like the main landing page for our site designed. We have provided a very simple wireframe to help provide direction for the content it should include, but we do not expect the designers to adhere to it at all - we encourage unique ideas. There is some sample text in the wireframe - this does not have to be used, but may provide ideas.

We provide an easy way for people to manage email for a custom domain name. For example if you own "yourhouseword.example" you can point your DNS records to us and we'll make it easy to have emails addressed to your domain get forwarded to your existing email (gmail, etc). Folks running blogs, and other small sites can quickly setup email addresses for their domains and manage them in one place.

(For technical folks, we have you point your dns mx records to us, hence the name. That way all your email hits us and we can redirect it wherever you want. We make it easy to manage a single domain or a bunch of domains. Many domain registrars offer this service for a fee, and have clumsy management tools. We provide a robust simple toolset for free, as well as premium options).

The goal of the landing page is to get folks into the signup flow. The second priority flow is to have them take a look at the premium plan offerings.

We may offer the winning designer additional work for the remainder of the site design.
Updates

I've changed this project to a committed payment.  It is no longer refundable.  Thank you.

Target Market(s)

Bloggers, podcasters, designers, app developers - people who are a little tech savvy.

Industry/Entity Type

It Company

Font styles to use
Sans Serif

Colors

Designer to choose colors to be used in the design.

Requirements
Must have
• A full fidelity mockup (comp) of the landing page including the source file (psd, ai, etc).

Some sort of logo treatment for the pingo.qz brand

A call to action for signup, such as the suggested 'Get Started Here'
Nice to have
• A hip startup feel

Incorporation of the email theme

Give the impression it is simple, easy and fast

```html
<!DOCTYPE html>
<html lang="en">
<head>
<meta charset="utf-8">
<title>Pingo.QZ — Email for your domain</title>
<link href="https://fonts.googleapis.com/css2?family=Open+Sans:wght@300;400;600;700;800&display=swap" rel="stylesheet">
<style>
  :root{
    --ink:#3f3f3f;
    --dark:#444546;
    --blue:#2aa3dd;
    --blue-deep:#1584bd;
    --link:#1e9bd8;
    --green:#7ac52a;
    --price:#7ab52e;
    --muted:#9a9a9a;
    --line:#e4e4e4;
    --white:#ffffff;
  }
  *{box-sizing:border-box;margin:0;padding:0}
  html,body{width:1200px;height:888px;overflow:hidden}
  body{font-family:"Open Sans",Arial,sans-serif;color:var(--ink);background:var(--white);position:relative}

  .site-header{position:absolute;left:0;top:0;width:1200px;height:88px;border-top:5px solid var(--dark);background:linear-gradient(#fff,#f3f3f3)}
  .brand{position:absolute;left:110px;top:20px;font-size:36px;font-weight:300;color:var(--blue);letter-spacing:-0.5px;line-height:44px}
  .main-nav{position:absolute;right:110px;top:10px;display:flex;height:73px}
  .main-nav a{display:flex;align-items:center;padding:0 21px;font-size:15px;color:#333;text-decoration:none;border-right:1px solid #e2e2e2}
  .main-nav a.is-active{color:var(--link)}

  .hero{position:absolute;left:0;top:88px;width:1200px;height:502px;border-bottom:5px solid var(--dark);
    background:radial-gradient(ellipse at 55% 40%,#4cc0f0 0%,var(--blue) 55%,#1f93cf 100%);overflow:hidden}
  .hero-photo{position:absolute;left:580px;top:42px;width:515px;height:460px;z-index:0;
    background:linear-gradient(160deg,rgba(255,255,255,0.3),rgba(30,30,30,0.5));border-radius:200px 200px 0 0}
  .hero-title,.hero-sub,.feature-list,.hero-actions,.offer,.price{z-index:1}
  .hero-title{position:absolute;left:110px;top:64px;font-size:47px;font-weight:700;color:var(--white);line-height:1;white-space:nowrap}
  .hero-sub{position:absolute;left:110px;top:130px;width:560px;font-size:22px;font-weight:700;color:var(--white);line-height:32px;text-transform:uppercase}
  .feature-list{position:absolute;left:110px;top:208px;width:450px;list-style:none;color:var(--white);font-size:13.6px;line-height:27px}
  .feature-list li{position:relative;padding-left:30px}
  .feature-list svg{position:absolute;left:0;top:5px}
  .hero-actions{position:absolute;left:110px;top:374px;display:flex;gap:8px}
  .btn{display:inline-block;height:46px;line-height:46px;padding:0 15px;font-size:16px;color:var(--white);text-decoration:none;text-transform:uppercase;border-radius:2px;white-space:nowrap}
  .btn strong{font-weight:700}
  .btn-start{background:var(--dark);min-width:171px}
  .btn-plans{background:var(--green);color:#222;min-width:162px}

  .offer{position:absolute;left:658px;top:230px;width:136px;height:136px;border-radius:50%;background:var(--blue-deep);color:var(--white);font-size:13px;line-height:20px;text-align:center;padding-top:22px}
  .offer em{font-style:normal;color:#b6f35a}
  .price{position:absolute;left:637px;top:298px;width:100px;height:100px;border-radius:50%;background:var(--white);text-align:center;color:#333;font-size:13px;padding-top:16px;line-height:16px}
  .price b{display:block;font-size:29px;line-height:34px;color:var(--price);font-weight:700}

  .guides{position:absolute;left:110px;top:618px;width:980px;height:190px}
  .guides .divider{position:absolute;left:490px;top:4px;width:1px;height:186px;background:var(--line)}
  .guide{position:absolute;top:0;width:432px}
  .guide.left{left:0}.guide.right{left:549px}
  .guide h2{font-size:23px;font-weight:400;line-height:29px;color:#444;height:75px;white-space:nowrap}
  .guide-card{display:flex;height:101px;border:1px solid var(--line)}
  .guide-mark{position:relative;flex:0 0 131px;background:#f6f6f6;display:flex;align-items:center;justify-content:center;gap:6px;font-size:14px;font-weight:700;color:#333}
  .guide-mark::after{content:"";position:absolute;right:-8px;top:42px;border:8px solid transparent;border-left-color:#f6f6f6;border-right:0}
  .guide-mark i{width:11px;height:11px;border-radius:50%;background:#f39a1e;flex:0 0 11px}
  .guide-text{padding:9px 18px 0 20px;font-size:12.5px;line-height:20px;color:var(--muted)}
  .guide-text a{color:var(--link);font-size:13px}

  .site-footer{position:absolute;left:0;top:840px;width:1200px;height:48px;background:var(--dark);color:#f1f1f1;font-size:13px;text-align:center;line-height:46px}
  .site-footer span{margin:0 9px;color:#bbb}
</style>
</head>
<body>
<header class="site-header">
  <div class="brand">Pingo.QZ</div>
  <nav class="main-nav">
    <a class="is-active" href="#">How it work</a>
    <a href="#">Support</a>
    <a href="#">Login</a>
  </nav>
</header>

<section class="hero">
  <div class="hero-photo" role="img" aria-label="Photo of a smiling businesswoman holding an open laptop and pointing toward the viewer"></div>
  <h1 class="hero-title">SELL US YOUR DOMAINS</h1>
  <p class="hero-sub">Lorem ipsum dolor sit amet, consectetur adipisicing elit.</p>
  <ul class="feature-list">
    <li><svg width="18" height="18" viewBox="0 0 18 18"><circle cx="9" cy="9" r="9" fill="#fff"/><path d="M5 9.3l2.6 2.6L13 6.5" stroke="#2aa3dd" stroke-width="2.2" fill="none"/></svg>We make email easy</li>
    <li><svg width="18" height="18" viewBox="0 0 18 18"><circle cx="9" cy="9" r="9" fill="#fff"/><path d="M5 9.3l2.6 2.6L13 6.5" stroke="#2aa3dd" stroke-width="2.2" fill="none"/></svg>Give us five minutes and we'll get you email from your domain</li>
    <li><svg width="18" height="18" viewBox="0 0 18 18"><circle cx="9" cy="9" r="9" fill="#fff"/><path d="M5 9.3l2.6 2.6L13 6.5" stroke="#2aa3dd" stroke-width="2.2" fill="none"/></svg>Easily forward mail from your custom domain name whereever you want it</li>
    <li><svg width="18" height="18" viewBox="0 0 18 18"><circle cx="9" cy="9" r="9" fill="#fff"/><path d="M5 9.3l2.6 2.6L13 6.5" stroke="#2aa3dd" stroke-width="2.2" fill="none"/></svg>Your take the mail, we'll keep the spam</li>
  </ul>
  <div class="hero-actions">
    <a class="btn btn-start" href="#">Get started <strong>free</strong></a>
    <a class="btn btn-plans" href="#">Compare <strong>plans</strong></a>
  </div>
  <div class="offer">get free <em>Domain</em><br>with Annual Plan</div>
  <div class="price">from only<b>$4.99</b>/month</div>
</section>

<section class="guides">
  <article class="guide left">
    <h2>How to Configure your SkyVeil<br>DNS to Us pingo.qz</h2>
    <div class="guide-card">
      <div class="guide-mark"><i></i>SkyVeil</div>
      <p class="guide-text">Lorem ipsum dolor sit amet, consectetur adipisicing elit, sed do eiusmod tempor incidi-dunt ut labore et dolore magna aliqua...<br><a href="#">Read More</a></p>
    </div>
  </article>
  <div class="divider"></div>
  <article class="guide right">
    <h2>Use pingo.qz with your DomainHive<br>domain Registration</h2>
    <div class="guide-card">
      <div class="guide-mark"><i></i>DomainHive</div>
      <p class="guide-text">Lorem ipsum dolor sit amet, consectetur adipisicing elit, sed do eiusmod tempor incidi-dunt ut labore et dolore magna aliqua...<br><a href="#">Read More</a></p>
    </div>
  </article>
</section>

<footer class="site-footer">
  2014, pingo.qz. Privacy Policy<span>|</span>Terms of Service<span>|</span>Help<span>|</span>Contact
</footer>
</body>
</html>
```